Updated website design needed for Radiology Group, Pine Hollow Imaging Partners

Clean, uncluttered, updated design needed for top regional Radiology Center. Focus on personal, patient oriented design, (not clinical). Should be simple and easy to navigate, with clear CTAs. Use blues, greens and photos of people in the Central Oregon outdoors.
Uncoded, PSD design only. 2 pages: Home page and one example interior page.
reference current site: http://www.phipclinic-example.com/
Sites they like:
http://www.valescanlabs-example.com/
http://www.tbmx-example.net/handler.cfm?event=practice,main
http://www.kestrelbonecare-example.com/

Medical Imaging

2 page

Sans Serif

• Personal and patient friendly.
• Lots of white space, clean and uncluttered. Clear CTAs, such as: Patient Bill Pay, Make an Appointment, Meet Our Doctors
• Use copy and contact information from the current site.
• Use outdoor images from Central Oregon, late Winter/ Spring (snow, light colors, spring green, for example)
• Include one example interior page, either Your Exam or Meet Our Doctors
• The client likes:
• Meet Our Doctors slider section, and big, easy to navigate Information Center on www.kestrelbonecare-example.com
• The personal feel of the Your Exam section on www.valescanlabs-example.com
• Blues and Greens, outdoorsy imagery
• The client does not like:
• complex drop down menus
• clinical feel
• Do not use lorum ipsum or dummy text.
• Do not use outdoor images from other regions. Do not use Summer (hot, poolside) or Fall (red/orange leaves) images.

```html
<!DOCTYPE html>
<html lang="en">
<head>
<meta charset="utf-8">
<title>Pine Hollow Imaging Partners</title>
<link rel="stylesheet" href="https://fonts.googleapis.com/css2?family=Roboto:wght@400;500;700&family=Oswald:wght@400;500&display=swap">
<style>
:root{
  --blue:#1e86c8;
  --nav-top:#2b95d3;
  --nav-bottom:#176fae;
  --green:#1f7a3c;
  --green-btn:#2e8a45;
  --ink:#222;
  --text:#666;
  --pale:#f1f2f3;
  --dark:#1b1b1b;
  --black:#0b0b0b;
  --white:#fff;
}
*{box-sizing:border-box;margin:0;padding:0}
html,body{width:1200px;height:2628px;overflow:hidden;background:var(--white)}
body{font-family:"Roboto",Arial,sans-serif;color:var(--text);position:relative}
.abs{position:absolute}

/* header */
.site-header{position:absolute;left:0;top:0;width:1200px;height:130px;background:var(--white)}
.brand{position:absolute;left:90px;top:38px;display:flex;align-items:center;gap:12px}
.brand-square{width:48px;height:48px;background:#6b6fa8}
.brand-name{font-size:22px;font-weight:500;color:#333;line-height:1.1;width:200px}
.phone{position:absolute;left:510px;top:44px;display:flex;align-items:center;gap:12px;font-size:21px;color:#333}
.phone svg{width:36px;height:36px}
.btn{position:absolute;display:flex;align-items:center;justify-content:center;color:var(--white);font-size:13px;font-weight:500;text-transform:uppercase;letter-spacing:.3px;border-radius:2px}
.btn-pay{left:737px;top:38px;width:174px;height:46px;background:var(--green-btn)}
.btn-appt{left:920px;top:38px;width:192px;height:46px;background:var(--dark)}

/* nav */
.main-nav{position:absolute;left:0;top:130px;width:1200px;height:68px;background:linear-gradient(var(--nav-top),var(--nav-bottom))}
.main-nav ul{list-style:none;display:flex;position:absolute;left:90px;top:0;height:68px}
.main-nav li{height:68px;display:flex;align-items:center;padding:0 19px;color:var(--white);font-size:13px;text-transform:uppercase}
.main-nav li.active{background:#1d2a33}

/* hero */
.hero{position:absolute;left:0;top:198px;width:1200px;height:530px;background:linear-gradient(180deg,#c9ccd0 0%,#e5e7ea 35%,#f4f5f7 70%,#e9ebee 100%)}
.hero-caption{position:absolute;left:658px;top:542px;width:454px;height:126px;background:rgba(90,90,90,.78);padding:20px 24px;font-family:"Oswald",Arial,sans-serif;color:var(--white)}
.hero-caption h2{font-size:36px;font-weight:400;line-height:1.1}
.hero-caption p{font-size:25px;line-height:1.3}
.hero-arrows{position:absolute;left:1052px;top:682px;display:flex;gap:2px}
.hero-arrows span{width:29px;height:34px;background:#333;display:flex;align-items:center;justify-content:center}

/* welcome */
.welcome{position:absolute;left:0;top:728px;width:1200px;height:515px;background:var(--pale)}
.welcome h1{position:absolute;left:0;top:52px;width:1200px;text-align:center;font-size:26px;font-weight:400;color:var(--ink)}
.welcome h1 em{font-style:normal;color:var(--green)}
.welcome .intro{position:absolute;left:92px;top:100px;width:1018px;text-align:center;font-size:13.5px;line-height:26px;color:var(--text)}
.feature{position:absolute;top:222px;width:320px;text-align:center}
.feature .ring{width:118px;height:118px;margin:0 auto;border-radius:50%;background:var(--white);border:2px solid #e2e4e6;box-shadow:0 0 0 6px #f7f8f9;display:flex;align-items:center;justify-content:center}
.feature h3{margin-top:26px;font-size:16px;font-weight:400;color:var(--ink);text-transform:uppercase}
.feature p{margin-top:12px;font-size:11.5px;line-height:19px;color:var(--text);padding:0 18px}

/* mammography */
.mammo{position:absolute;left:0;top:1243px;width:1200px;height:410px;background:var(--white)}
.video{position:absolute;left:93px;top:52px;width:490px;height:302px;border:1px solid #ccc;box-shadow:0 1px 4px rgba(0,0,0,.25);background:var(--white);padding:12px}
.video-screen{position:relative;width:100%;height:100%;background:#0f2a30;overflow:hidden}
.video-left{position:absolute;left:0;top:0;width:226px;height:240px;background:linear-gradient(135deg,#1f5560,#2a6b6e)}
.video-right{position:absolute;left:226px;top:0;width:240px;height:240px;background:linear-gradient(135deg,#777,#3b3b3b)}
.video-bar{position:absolute;left:0;bottom:0;width:100%;height:36px;background:#121212;display:flex;align-items:center;padding:0 10px;gap:10px;color:#ddd;font-size:10px}
.mammo h2{position:absolute;left:608px;top:62px;font-size:22px;font-weight:500;color:var(--green);text-transform:uppercase}
.mammo .copy{position:absolute;left:608px;top:102px;width:508px;font-size:12.5px;line-height:24px;color:#444}
.mammo .copy p+p{margin-top:8px}
.btn-doctors{left:608px;top:297px;width:175px;height:40px;background:var(--blue);font-size:14px;text-transform:none}

/* services */
.services{position:absolute;left:0;top:1653px;width:1200px;height:485px;background:var(--pale)}
.services h2{position:absolute;left:0;top:38px;width:1200px;text-align:center;font-size:26px;font-weight:400;color:var(--ink);text-transform:uppercase}
.services h2 em{font-style:normal;color:var(--green)}
.services .lead{position:absolute;left:0;top:84px;width:1200px;text-align:center;font-size:13px;color:#555}
.round-arrow{position:absolute;top:44px;width:34px;height:34px;border-radius:50%;background:var(--white);border:1px solid #ccc;display:flex;align-items:center;justify-content:center}
.card{position:absolute;top:134px;width:318px}
.card .photo{width:318px;height:195px;border:1px solid #ddd;padding:4px;background:var(--white)}
.card .photo div{width:100%;height:100%}
.card h3{margin-top:16px;font-size:15px;font-weight:400;color:var(--ink)}
.card p{margin-top:10px;font-size:11.5px;line-height:19px;color:var(--text)}
.card a{display:block;margin-top:10px;font-size:11.5px;color:var(--green);text-decoration:none}

/* partners */
.partners{position:absolute;left:0;top:2138px;width:1200px;height:142px;background:var(--white)}
.partner{position:absolute;top:54px;height:34px;background:#b8b8b8;border-radius:3px}

/* footer */
.site-footer{position:absolute;left:0;top:2280px;width:1200px;height:267px;background:var(--blue)}
.f-col{position:absolute;top:32px;color:var(--white)}
.f-col h4{font-size:13.5px;font-weight:500;text-transform:uppercase;margin-bottom:14px}
.f-col ul{list-style:none}
.f-col li{font-size:11.5px;line-height:26px;color:#e6f1f9}
.f-col li::before{content:"»";margin-right:7px}
.f-col.contact li::before{content:none}
.f-col.contact li svg{vertical-align:-2px;margin-right:6px}
.social li{display:flex;align-items:center;gap:14px;line-height:1;margin-bottom:11px}
.social li::before{content:none}
.social .dot{width:32px;height:32px;border-radius:50%;border:1.5px solid #cfe4f3}
.copyright{position:absolute;left:0;top:2547px;width:1200px;height:81px;background:var(--black);color:#ddd;font-size:11.5px;display:flex;align-items:center;justify-content:center}
</style>
</head>
<body>

<header class="site-header">
  <div class="brand"><div class="brand-square"></div><div class="brand-name">Pine Hollow Imaging Partners</div></div>
  <div class="phone">
    <svg viewBox="0 0 36 36"><circle cx="18" cy="18" r="16.5" fill="none" stroke="#2e8a45" stroke-width="1.5"/><path d="M12.5 11c1-.6 2-.5 2.6.4l1.5 2.3c.5.8.3 1.7-.4 2.2l-1 .7c.8 2 2.3 3.6 4.3 4.5l.8-1c.5-.7 1.5-.9 2.2-.4l2.3 1.5c.9.6 1 1.7.4 2.6-1.2 1.7-3.3 2.2-5.2 1.3-3.5-1.7-6.2-4.4-7.9-7.9-.9-1.9-.4-4 .4-6.2z" fill="#2e8a45"/></svg>
    <span>(555) 214-7730</span>
  </div>
  <div class="btn btn-pay">Patient Bill Pay</div>
  <div class="btn btn-appt">Make an Appointment</div>
</header>

<nav class="main-nav">
  <ul>
    <li class="active">Home</li><li>About Us</li><li>Our Services</li><li>For Patients</li><li>Our Physicians</li><li>For Physicians</li><li>Appointments</li><li>Our Locations</li>
  </ul>
</nav>

<section class="hero" role="img" aria-label="Photo of two hikers walking a snowy forest trail in late winter"></section>
<div class="hero-caption"><h2>REGIONAL RADIOLOGY CENTER</h2><p>Expert imaging care close to home</p></div>
<div class="hero-arrows">
  <span><svg width="10" height="14" viewBox="0 0 10 14"><path d="M8 1L2 7l6 6" stroke="#fff" stroke-width="1.6" fill="none"/></svg></span>
  <span><svg width="10" height="14" viewBox="0 0 10 14"><path d="M2 1l6 6-6 6" stroke="#fff" stroke-width="1.6" fill="none"/></svg></span>
</div>

<section class="welcome">
  <h1>WELCOME TO <em>PINE HOLLOW IMAGING PARTNERS</em></h1>
  <p class="intro">Pine Hollow Imaging Partners is a diagnostic imaging corporation providing professional services to Central and Eastern Oregon hospitals and clinics as well as state-of-the-art services in its own outpatient imaging center. PHIP was established by its founder, Walter H. Brenning, MD when he opened his Central Oregon practice in 1947 and is staffed by fellowship trained physicians with expertise in major disciplines to include mammography, ultrasound, Magnetic</p>

  <div class="feature" style="left:75px">
    <div class="ring"><svg width="34" height="34" viewBox="0 0 34 34"><path d="M3 16L31 4 24 30l-7-8-4 6v-9l14-13L12 17z" fill="#1e86c8"/></svg></div>
    <h3>Online Bill Pay</h3>
    <p>Pay your imaging bill securely online in a few minutes, any time of day, with no need to call or mail a check.</p>
  </div>
  <div class="feature" style="left:438px">
    <div class="ring"><svg width="34" height="34" viewBox="0 0 34 34"><rect x="3" y="9" width="28" height="20" rx="3" fill="#1e86c8"/><rect x="12" y="4" width="10" height="6" rx="1.5" fill="none" stroke="#1e86c8" stroke-width="2"/><path d="M15 13h4v4h4v4h-4v4h-4v-4h-4v-4h4z" fill="#fff"/></svg></div>
    <h3>What We Do</h3>
    <p>We read MRI, CT, ultrasound, mammography and X-ray exams for hospitals and clinics across the region.</p>
  </div>
  <div class="feature" style="left:796px">
    <div class="ring"><svg width="34" height="34" viewBox="0 0 34 34"><circle cx="17" cy="17" r="12" fill="none" stroke="#1e86c8" stroke-width="5"/><circle cx="17" cy="17" r="5" fill="#fff" stroke="#1e86c8" stroke-width="2"/></svg></div>
    <h3>For Physicians</h3>
    <p>Order exams, view images and reach our radiologists quickly through secure referral tools for your practice.</p>
  </div>
</section>

<section class="mammo">
  <div class="video">
    <div class="video-screen">
      <div class="video-left" role="img" aria-label="Illustration of a patient in profile"></div>
      <div class="video-right" role="img" aria-label="Grayscale mammogram scan"></div>
      <svg class="abs" style="left:206px;top:98px" width="44" height="44" viewBox="0 0 44 44"><circle cx="22" cy="22" r="21" fill="rgba(0,0,0,.75)"/><path d="M17 13l13 9-13 9z" fill="#fff"/></svg>
      <div class="video-bar">
        <svg width="14" height="14" viewBox="0 0 14 14"><circle cx="7" cy="7" r="6" fill="none" stroke="#ddd" stroke-width="1.5"/><path d="M5.5 4l4 3-4 3z" fill="#ddd"/></svg>
        <svg width="40" height="10" viewBox="0 0 40 10"><path d="M0 3h3l3-3v10L3 7H0z" fill="#e05"/><path d="M10 5h28" stroke="#e05" stroke-width="2" stroke-dasharray="2 2"/></svg>
        <div style="flex:1;height:3px;background:#555"><div style="width:35%;height:3px;background:#e0245e"></div></div>
        <span>01:30 / 04:55</span>
        <svg width="12" height="10" viewBox="0 0 12 10"><rect x="1" y="1" width="10" height="8" fill="none" stroke="#ddd"/></svg>
        <svg width="12" height="12" viewBox="0 0 12 12"><circle cx="6" cy="6" r="4" fill="none" stroke="#ddd" stroke-width="2" stroke-dasharray="2 1.2"/></svg>
      </div>
    </div>
  </div>
  <h2>What is 3D Mammography?</h2>
  <div class="copy">
    <p>3D mammography, also called breast tomosynthesis, takes a series of thin images of the breast from several angles. Our radiologists review these layers one at a time, which makes small cancers easier to find and lowers the chance of a call back for more pictures.</p>
    <p>The exam feels much like a standard mammogram and adds only a few seconds. Most insurance plans cover it, and our friendly staff will guide you through every step of your visit.</p>
  </div>
  <div class="btn btn-doctors">Meet Our Doctors</div>
</section>

<section class="services">
  <div class="round-arrow" style="left:78px"><svg width="10" height="12" viewBox="0 0 10 12"><path d="M7 1L2 6l5 5" stroke="#222" stroke-width="2" fill="none"/></svg></div>
  <div class="round-arrow" style="left:1086px"><svg width="10" height="12" viewBox="0 0 10 12"><path d="M3 1l5 5-5 5" stroke="#222" stroke-width="2" fill="none"/></svg></div>
  <h2>Our <em>Service</em></h2>
  <p class="lead">Comfortable, accurate exams read by our fellowship trained radiologists</p>

  <article class="card" style="left:88px">
    <div class="photo"><div role="img" aria-label="Photo of an MRI workstation with brain scan on screen" style="background:linear-gradient(135deg,#7fc4ea,#2f7fc0)"></div></div>
    <h3>Magnetic Resonance Imaging (MRI)</h3>
    <p>MRI uses a strong magnet and radio waves to create detailed pictures of the brain, spine, joints and organs.</p>
    <a>Read More »</a>
  </article>
  <article class="card" style="left:441px">
    <div class="photo"><div role="img" aria-label="Photo of a patient in a CT scanner with a technician" style="background:linear-gradient(135deg,#e9f1f7,#a9cde6)"></div></div>
    <h3>Computed Tomography (CT)</h3>
    <p>Our CT scanner captures fast, low-dose cross-section images of the body to help your doctor guide your care.</p>
    <a>Read More »</a>
  </article>
  <article class="card" style="left:794px">
    <div class="photo"><div role="img" aria-label="Photo of a smiling sonographer beside an ultrasound machine" style="background:linear-gradient(135deg,#f3f4f6,#8fb6d6)"></div></div>
    <h3>Ultrasound</h3>
    <p>Ultrasound uses safe sound waves to view organs, blood flow and pregnancies, with no radiation at all.</p>
    <a>Read More »</a>
  </article>
</section>

<section class="partners" aria-label="Partners">
  <div class="partner" style="left:128px;width:68px"></div>
  <div class="partner" style="left:254px;width:116px"></div>
  <div class="partner" style="left:430px;width:104px"></div>
  <div class="partner" style="left:598px;width:110px"></div>
  <div class="partner" style="left:793px;width:84px"></div>
  <div class="partner" style="left:952px;width:118px"></div>
</section>

<footer class="site-footer">
  <div class="f-col" style="left:92px"><h4>For Patients</h4><ul><li>About Your Visit</li><li>Why Choose Us?</li><li>Patient Forms</li><li>Billing and Insurance</li><li>Locations and Maps</li><li>Appointments</li></ul></div>
  <div class="f-col" style="left:325px"><h4>Quick Links</h4><ul><li>Home</li><li>About Us</li><li>Our Physicians</li><li>For Physicians</li><li>Disclaimer</li><li>HIPAA</li></ul></div>
  <div class="f-col" style="left:527px"><h4>Our Services</h4><ul><li>Our Services</li><li>Mammography</li><li>MRI</li><li>CT-64</li><li>X-Ray</li><li>Nuclear Medicine</li></ul></div>
  <div class="f-col contact" style="left:735px"><h4>Our Services</h4><ul>
    <li><svg width="11" height="11" viewBox="0 0 12 12"><path d="M2 1l2 0 1 3-1.5 1c.7 1.5 1.9 2.7 3.5 3.5L8 7l3 1v2c0 .6-.5 1-1 1C5 11 1 7 1 2c0-.5.5-1 1-1z" fill="#fff"/></svg>(555) 214-7730 - Main Line</li>
    <li><svg width="11" height="11" viewBox="0 0 12 12"><path d="M2 1l2 0 1 3-1.5 1c.7 1.5 1.9 2.7 3.5 3.5L8 7l3 1v2c0 .6-.5 1-1 1C5 11 1 7 1 2c0-.5.5-1 1-1z" fill="#fff"/></svg>(555) 214-7741 - Scheduling</li>
    <li><svg width="11" height="11" viewBox="0 0 12 12"><path d="M2 1l2 0 1 3-1.5 1c.7 1.5 1.9 2.7 3.5 3.5L8 7l3 1v2c0 .6-.5 1-1 1C5 11 1 7 1 2c0-.5.5-1 1-1z" fill="#fff"/></svg>(555) 214-7752 - Billing</li>
    <li><svg width="11" height="11" viewBox="0 0 12 12"><path d="M2 1l2 0 1 3-1.5 1c.7 1.5 1.9 2.7 3.5 3.5L8 7l3 1v2c0 .6-.5 1-1 1C5 11 1 7 1 2c0-.5.5-1 1-1z" fill="#fff"/></svg>(555) 214-7763 - Medical Records</li>
  </ul></div>
  <div class="f-col social" style="left:1008px"><h4>Follow Us On</h4><ul>
    <li><span class="dot"></span>Chatterly</li>
    <li><span class="dot"></span>Chirpline</li>
    <li><span class="dot"></span>Pictorama</li>
  </ul></div>
</footer>
<div class="copyright">Copyright © 2016. All Rights Reserved</div>

</body>
</html>
```